Wordpress Design for a Private Label BBQ Brand

For our new brand, we'd need a new Wordpress website. We'd prefer to run the website on Wordpress

We'd like to include the following
- space for description of the brand
- space for product portfolio (not a shop!)
- space for socials
- space for support
- space for contact

```html
<!DOCTYPE html>
<html lang="en">
<head>
<meta charset="utf-8">
<title>Emberly BBQ</title>
<link href="https://fonts.googleapis.com/css2?family=Libre+Baskerville:wght@400;700&family=Jost:wght@400;500&display=swap" rel="stylesheet">
<style>
:root{
  --red:#d83a1f;
  --red-deep:#c5241e;
  --orange:#ea5a1d;
  --ink:#1d1d1d;
  --text:#444;
  --muted:#8a8a8a;
  --cream:#fbf6f3;
  --field:#ececec;
  --night:#0b0b0b;
  --white:#fff;
}
*{box-sizing:border-box;margin:0;padding:0}
html,body{width:1200px;height:5042px;overflow:hidden;background:var(--white)}
body{font-family:"Jost",sans-serif;color:var(--text)}
.canvas{position:relative;width:1200px;height:5042px;overflow:hidden}
.abs{position:absolute}
.serif{font-family:"Libre Baskerville",serif;font-weight:700}
section,header,footer{position:absolute;left:0;width:1200px}

/* top bar */
.topbar{top:0;height:49px;background:#151515;color:var(--white);font-size:15px}
.topbar .dot{position:absolute;top:17px;width:15px;height:15px;border:2px solid var(--orange);border-radius:50%}
.topbar .info{position:absolute;top:13px;display:flex;align-items:center;gap:10px}
.topbar b{font-weight:500}

/* nav */
.nav{top:49px;height:96px;background:var(--white)}
.brand{position:absolute;display:flex;align-items:center;gap:12px}
.brand .mark{width:30px;height:30px;border-radius:50%;background:var(--red)}
.brand .name{font-family:"Libre Baskerville",serif;font-weight:700;font-size:34px;color:var(--ink)}
.menu a{position:absolute;top:38px;font-family:"Libre Baskerville",serif;font-weight:700;font-size:15px;letter-spacing:1px;color:#333;text-decoration:none;white-space:nowrap}
.menu .active::before{content:"";position:absolute;left:50%;top:-22px;width:10px;height:10px;margin-left:-5px;border-radius:50%;background:var(--red)}

/* buttons */
.btn{position:absolute;display:flex;align-items:center;border-radius:40px;font-family:"Libre Baskerville",serif;font-weight:700;font-size:16px;letter-spacing:1px;color:var(--white);white-space:nowrap}
.btn .label{flex:1;padding-left:28px}
.btn .knob{width:50px;height:50px;margin-right:4px;border-radius:50%;background:var(--white);display:flex;align-items:center;justify-content:center}
.btn-solid{background:linear-gradient(90deg,var(--red-deep),var(--orange))}
.btn-line{border:3px solid var(--white)}

/* hero */
.hero{top:145px;height:614px;background:linear-gradient(100deg,#d8421f 0%,#e2512a 55%,#ee6a2a 100%)}
.hero h1{position:absolute;left:94px;top:168px;font-size:66px;color:var(--white);letter-spacing:1px;white-space:nowrap}
.hero p{position:absolute;left:94px;top:272px;width:560px;font-size:21px;line-height:33px;color:var(--white)}
.hero-art{position:absolute;left:660px;top:12px;width:540px;height:602px;border-radius:60% 40% 0 0 / 70% 50% 0 0;background:linear-gradient(160deg,#7f8f9a,#b3763f 55%,#6b5a4f)}
.slide-arrow{position:absolute}

/* about */
.about{top:759px;height:656px;background:var(--cream)}
.about-frame{position:absolute;left:121px;top:96px;width:419px;height:429px;border:5px solid var(--red)}
.about-photo{position:absolute;left:94px;top:78px;width:425px;height:425px;border-radius:80px 0 0 0;background:linear-gradient(150deg,#1a1412,#5a2a17 50%,#c2561f)}
.about h2{position:absolute;left:601px;top:142px;font-size:38px;color:var(--ink);white-space:nowrap}
.about p{position:absolute;left:601px;top:213px;width:510px;font-size:21px;line-height:32px}

/* highlight */
.highlight{top:1415px;height:894px;background:linear-gradient(180deg,#050505 0%,#120806 45%,#5a1d08 78%,#d0580f 100%)}
.highlight h2{position:absolute;width:1200px;top:74px;text-align:center;font-size:40px;color:var(--white)}
.feat-text{position:absolute;font-size:21px;line-height:32px;color:var(--white);white-space:nowrap}
.feat-dot{position:absolute;width:102px;height:102px;border-radius:50%;border:3px solid #3a3a3a;background:radial-gradient(circle at 40% 35%,#6a6a6a,#151515)}
.hub-ring{position:absolute;left:409px;top:372px;width:380px;height:380px;border-radius:50%;border:4px solid var(--orange)}
.hub-core{position:absolute;left:433px;top:396px;width:332px;height:332px;border-radius:50%;background:linear-gradient(135deg,var(--orange),var(--red-deep))}
.hub-product{position:absolute;left:497px;top:400px;width:204px;height:330px;border-radius:90px 90px 20px 20px;background:linear-gradient(180deg,#3a3a3a,#0e0e0e)}

/* portfolio */
.portfolio{top:2309px;height:754px;background:var(--white)}
.portfolio h2{position:absolute;left:94px;top:76px;font-size:40px;color:var(--ink)}
.portfolio .lead{position:absolute;left:94px;top:146px;width:560px;font-size:21px;line-height:32px}
.card{position:absolute;top:276px;width:233px;height:394px;background:var(--white);border-radius:6px;box-shadow:0 8px 26px rgba(0,0,0,.07);text-align:center}
.card.current{border:2px solid var(--orange)}
.card .badge{position:absolute;left:76px;top:-22px;width:80px;height:80px;border-radius:50%;background:linear-gradient(135deg,var(--red-deep),var(--orange))}
.card .shot{position:absolute;left:56px;top:80px;width:121px;height:137px;border-radius:8px;background:linear-gradient(180deg,#d6d6d6,#3a3a3a)}
.card h3{position:absolute;width:100%;top:256px;font-size:18px;color:var(--ink);white-space:nowrap}
.card .rule{position:absolute;left:88px;top:290px;width:56px;height:2px;background:var(--orange)}
.card p{position:absolute;width:100%;top:308px;font-size:20px;line-height:31px;color:#555}

/* support */
.support{top:3063px;height:528px;background:linear-gradient(100deg,#c5241e,#e2431f 50%,#ec5e1c)}
.support h2{position:absolute;left:94px;top:90px;font-size:40px;line-height:47px;color:var(--white)}
.support p{position:absolute;left:94px;top:195px;width:470px;font-size:21px;line-height:32px;color:var(--white)}
.support .rule{position:absolute;left:94px;top:327px;width:211px;height:1px;background:rgba(255,255,255,.35)}
.call{position:absolute;left:94px;top:352px;display:flex;align-items:center;gap:20px;font-size:21px;color:var(--white)}
.call .ring{width:66px;height:66px;border-radius:50%;border:3px solid var(--white);display:flex;align-items:center;justify-content:center}

/* instagram strip */
.gallery{top:3591px;height:239px}
.tile{position:absolute;top:0;width:240px;height:239px}
.tile.follow{left:240px;background:#2b2b2b}
.follow .sq{position:absolute;left:38px;top:68px;width:28px;height:28px;border:3px solid var(--orange);border-radius:7px}
.follow span.serif{position:absolute;left:38px;top:116px;font-size:18px;line-height:30px;color:var(--white)}

/* contact */
.contact{top:3830px;height:773px;background:var(--cream)}
.contact h2{position:absolute;width:1200px;top:76px;text-align:center;font-size:40px;color:var(--ink)}
.contact .lead{position:absolute;width:1200px;top:150px;text-align:center;font-size:21px;line-height:32px}
.field{position:absolute;background:var(--field);border-radius:3px;padding:16px 18px;font-size:19px;color:#9a9a9a}

/* footer */
.footer{top:4603px;height:439px;background:var(--night);color:#aaa}
.footer h4{position:absolute;top:86px;font-size:18px;letter-spacing:.5px;color:var(--white)}
.footer ul{position:absolute;top:138px;list-style:none;font-size:19px;line-height:32px}
.footer .brand{left:94px;top:120px;width:170px;flex-direction:column;align-items:center;gap:26px}
.footer .brand .name{color:var(--white);font-size:32px}
.footer .row{position:absolute;left:881px;display:flex;align-items:center;gap:20px;font-size:19px;color:#bbb}
.soc{position:absolute;top:231px;width:46px;height:46px;border-radius:50%;background:linear-gradient(135deg,var(--red-deep),var(--orange))}
.copy{position:absolute;width:1200px;top:365px;text-align:center;font-size:14px;letter-spacing:.5px;color:#777}
</style>
</head>
<body>
<div class="canvas">

  <header class="topbar">
    <span class="dot" style="left:92px"></span>
    <span class="dot" style="left:122px"></span>
    <span class="dot" style="left:156px"></span>
    <span class="dot" style="left:190px"></span>
    <div class="info" style="left:464px">
      <svg width="18" height="14" viewBox="0 0 18 14"><rect x="1" y="1" width="16" height="12" rx="1" fill="none" stroke="#ea5a1d" stroke-width="2"/><path d="M1 1l8 7 8-7" fill="none" stroke="#ea5a1d" stroke-width="2"/></svg>
      <span>Email Us: <b>support@emberly.com</b></span>
    </div>
    <div class="info" style="left:902px">
      <svg width="16" height="16" viewBox="0 0 24 24"><path d="M6.6 10.8a15 15 0 006.6 6.6l2.2-2.2c.3-.3.7-.4 1-.2 1.1.4 2.3.6 3.6.6.6 0 1 .4 1 1V20c0 .6-.4 1-1 1A17 17 0 013 4c0-.6.4-1 1-1h3.5c.6 0 1 .4 1 1 0 1.3.2 2.5.6 3.6.1.3 0 .7-.2 1z" fill="#ea5a1d"/></svg>
      <span>Call Us: <b>123-456-7890</b></span>
    </div>
  </header>

  <header class="nav">
    <div class="brand" style="left:92px;top:29px">
      <span class="mark"></span><span class="name">EMBERLY</span>
    </div>
    <nav class="menu">
      <a class="active" style="left:456px">HOME</a>
      <a style="left:548px">ABOUT</a>
      <a style="left:650px">SUPPORT</a>
      <a style="left:774px">PRODUCT PORTFOLIO</a>
      <a style="left:1016px">CONTACT</a>
    </nav>
  </header>

  <section class="hero">
    <div class="hero-art" role="img" aria-label="Grilled steaks on a barbecue grate framed in a flame shape"></div>
    <h1 class="serif">EMBERLY BBQ</h1>
    <p>Duis aute irure dolor in reprehenderit in voluptateos velit esse cillum dolore eu fugiat nulla.</p>
    <div class="btn btn-line" style="left:94px;top:368px;width:260px;height:58px">
      <span class="label">VIEW PRODUCT</span>
      <span class="knob" style="width:44px;height:44px;background:none"><svg width="22" height="22" viewBox="0 0 22 22"><path d="M4 11h13M12 6l5 5-5 5" fill="none" stroke="#fff" stroke-width="2.4"/></svg></span>
    </div>
    <svg class="slide-arrow" style="left:20px;top:278px" width="28" height="56" viewBox="0 0 28 56"><path d="M26 2L2 28l24 26" fill="none" stroke="#fff" stroke-width="3"/></svg>
    <svg class="slide-arrow" style="left:1152px;top:278px" width="28" height="56" viewBox="0 0 28 56"><path d="M2 2l24 26L2 54" fill="none" stroke="#fff" stroke-width="3"/></svg>
  </section>

  <section class="about">
    <div class="about-frame"></div>
    <div class="about-photo" role="img" aria-label="Grilled steak with rosemary over open flames and a barbecue fork"></div>
    <h2 class="serif">ABOUT EMBERLY BBQ</h2>
    <p>Duis aute irure dolor in reprehenderit in voluptateos velit esse cillum dolore eu fugiat nulla pariatur.Epteo sint occaecat cupidatat non proident sunt in culpatoi qui officia deserunt mollit anim id est laborum. Sedo ut perspiciatis unde omnis iste natus error sit volupt tem accusantium doloremque laudantium.</p>
    <div class="btn btn-solid" style="left:601px;top:429px;width:219px;height:58px">
      <span class="label">READ MORE</span>
      <span class="knob"><svg width="22" height="22" viewBox="0 0 22 22"><path d="M4 11h13M12 6l5 5-5 5" fill="none" stroke="#d83a1f" stroke-width="2.4"/></svg></span>
    </div>
  </section>

  <section class="highlight" role="group" aria-label="Product highlight">
    <h2 class="serif">PRODUCT HIGHLIGHT</h2>
    <div class="hub-ring"></div>
    <div class="hub-core"></div>
    <div class="hub-product" role="img" aria-label="Black ceramic kamado grill on a steel stand"></div>

    <div class="feat-text" style="left:400px;top:168px;width:400px;text-align:center">Bottom damper to control<br>airflow for temparature</div>
    <div class="feat-dot" style="left:548px;top:242px" role="img" aria-label="Bottom damper detail"></div>

    <div class="feat-text" style="left:20px;top:365px;width:300px;text-align:right">Adjustable to damper<br>maintains airflow</div>
    <div class="feat-dot" style="left:342px;top:344px" role="img" aria-label="Top damper detail"></div>

    <div class="feat-text" style="left:20px;top:496px;width:247px;text-align:right">Heat insulation<br>handle</div>
    <div class="feat-dot" style="left:290px;top:477px" role="img" aria-label="Insulated handle detail"></div>

    <div class="feat-text" style="left:20px;top:638px;width:259px;text-align:right">Stripes designed<br>to increase beauty</div>
    <div class="feat-dot" style="left:303px;top:618px" role="img" aria-label="Textured surface detail"></div>

    <div class="feat-dot" style="left:757px;top:344px" role="img" aria-label="Thermometer detail"></div>
    <div class="feat-text" style="left:881px;top:365px">Temperature changes<br>from the thermometer</div>

    <div class="feat-dot" style="left:810px;top:477px" role="img" aria-label="Hinge detail"></div>
    <div class="feat-text" style="left:934px;top:496px">Preminun hinge<br>material - Iron</div>

    <div class="feat-dot" style="left:798px;top:618px;background:radial-gradient(circle,#fff 55%,#ddd)" role="img" aria-label="Stainless steel cart detail"></div>
    <div class="feat-text" style="left:922px;top:638px">Stainless steel<br>mobile cart</div>
  </section>

  <section class="portfolio">
    <h2 class="serif">PRODUCT PORTFOLIO</h2>
    <p class="lead">Duis aute irure dolor in reprehenderit in voluptateos velit esse cillum dolore eu fugiat nulla pariatur.</p>
    <div class="btn btn-solid" style="left:885px;top:80px;width:221px;height:59px">
      <span class="label">VIEW MORE</span>
      <span class="knob"><svg width="22" height="22" viewBox="0 0 22 22"><path d="M4 11h13M12 6l5 5-5 5" fill="none" stroke="#d83a1f" stroke-width="2.4"/></svg></span>
    </div>

    <article class="card" style="left:92px"><span class="badge"></span><div class="shot" role="img" aria-label="Three piece barbecue tool set"></div><h3 class="serif">EMBERLY-3PC-1</h3><span class="rule"></span><p>Lotem unde omnis<br>is iste natus error.</p></article>
    <article class="card current" style="left:352px"><span class="badge"></span><div class="shot" role="img" aria-label="Pair of grill handles"></div><h3 class="serif">EMBERLY-3PC-1</h3><span class="rule"></span><p>Lotem unde omnis<br>is iste natus error.</p></article>
    <article class="card" style="left:614px"><span class="badge"></span><div class="shot" role="img" aria-label="Fifteen piece barbecue tool case"></div><h3 class="serif">EMBERLY-15PCS-1</h3><span class="rule"></span><p>Lotem unde omnis<br>is iste natus error.</p></article>
    <article class="card" style="left:875px"><span class="badge"></span><div class="shot" role="img" aria-label="Thirteen inch kamado grill"></div><h3 class="serif" style="font-size:17px">EMBERLY-13INCH-8</h3><span class="rule"></span><p>Lotem unde omnis<br>is iste natus error.</p></article>

    <svg class="abs" style="left:40px;top:448px" width="26" height="52" viewBox="0 0 26 52"><path d="M24 2L2 26l22 24" fill="none" stroke="#333" stroke-width="3"/></svg>
    <svg class="abs" style="left:1134px;top:448px" width="26" height="52" viewBox="0 0 26 52"><path d="M2 2l22 24L2 50" fill="none" stroke="#333" stroke-width="3"/></svg>
  </section>

  <section class="support">
    <h2 class="serif">NEED ANY KIND<br>OF SUPPORT</h2>
    <p>Lorem ipsum dolor sit amet, consectetur adipis el sed do eiusmod tempor incididunt ut labore eto dolore magna aliqua. Ut enim ad min.</p>
    <span class="rule"></span>
    <div class="call">
      <span class="ring"><svg width="26" height="26" viewBox="0 0 24 24"><path d="M6.6 10.8a15 15 0 006.6 6.6l2.2-2.2c.3-.3.7-.4 1-.2 1.1.4 2.3.6 3.6.6.6 0 1 .4 1 1V20c0 .6-.4 1-1 1A17 17 0 013 4c0-.6.4-1 1-1h3.5c.6 0 1 .4 1 1 0 1.3.2 2.5.6 3.6.1.3 0 .7-.2 1z" fill="#fff"/></svg></span>
      <span>Call Us: <b style="font-weight:500">123-456-7890</b></span>
    </div>
    <svg class="abs" style="left:648px;top:80px" width="462" height="370" viewBox="0 0 462 370">
      <defs><linearGradient id="deskTone" x1="0" y1="0" x2="1" y2="1"><stop offset="0" stop-color="#e9e6e2"/><stop offset=".6" stop-color="#b9b6b3"/><stop offset="1" stop-color="#7d7a78"/></linearGradient></defs>
      <polygon points="64,10 54,10 4,185 54,360 64,360 14,185" fill="#fff"/>
      <polygon role="img" aria-label="Support agents wearing headsets at laptops" points="130,0 362,0 458,185 362,370 130,370 34,185" fill="url(#deskTone)"/>
    </svg>
  </section>

  <section class="gallery">
    <div class="tile" style="left:0;background:linear-gradient(160deg,#1a0e08,#c6471a 50%,#f0a02c)" role="img" aria-label="Flames rising from a grill"></div>
    <div class="tile follow"><span class="sq"></span><span class="serif">FOLLOW US<br>ON INSTAGRAM</span></div>
    <div class="tile" style="left:480px;background:linear-gradient(180deg,#6a8a4a,#5a6d78 55%,#203040)" role="img" aria-label="Kamado grill in a garden"></div>
    <div class="tile" style="left:720px;background:linear-gradient(170deg,#2a140a,#d05a18 55%,#f2a032)" role="img" aria-label="Grill grate over flames"></div>
    <div class="tile" style="left:960px;background:radial-gradient(circle,#1f2428 30%,#cfd3d6 70%,#e9ecee)" role="img" aria-label="Charcoal in the grill basket"></div>
  </section>

  <section class="contact">
    <h2 class="serif">CONTACT US</h2>
    <p class="lead">Duis aute irure dolor in reprehenderit in voluptateos<br>velit esse cillum dolore eu fugiat nulla pariatur.</p>
    <div class="field" style="left:243px;top:254px;width:348px;height:59px">First Name</div>
    <div class="field" style="left:609px;top:254px;width:348px;height:59px">Last Name</div>
    <div class="field" style="left:243px;top:330px;width:348px;height:57px">Phone No</div>
    <div class="field" style="left:609px;top:330px;width:348px;height:57px">Email Address</div>
    <div class="field" style="left:243px;top:405px;width:714px;height:184px">Message</div>
    <div class="btn btn-solid" style="left:483px;top:626px;width:233px;height:59px">
      <span class="label">SUBMIT NOW</span>
      <span class="knob"><svg width="22" height="22" viewBox="0 0 22 22"><path d="M4 11h13M12 6l5 5-5 5" fill="none" stroke="#d83a1f" stroke-width="2.4"/></svg></span>
    </div>
  </section>

  <footer class="footer">
    <div class="brand">
      <span class="mark" style="width:54px;height:54px"></span>
      <span class="name">EMBERLY</span>
    </div>
    <h4 class="serif" style="left:366px">QUICK LINKS</h4>
    <ul style="left:366px"><li>About</li><li>Support</li><li>Product Portfolio</li><li>Contact</li></ul>
    <h4 class="serif" style="left:615px">OTHER LINKS</h4>
    <ul style="left:615px"><li>Privacy Policy</li><li>FAQ</li><li>Terms &amp; Condition</li><li>Blog</li></ul>
    <h4 class="serif" style="left:881px">CONTACT US</h4>
    <div class="row" style="top:136px">
      <svg width="18" height="18" viewBox="0 0 24 24"><path d="M6.6 10.8a15 15 0 006.6 6.6l2.2-2.2c.3-.3.7-.4 1-.2 1.1.4 2.3.6 3.6.6.6 0 1 .4 1 1V20c0 .6-.4 1-1 1A17 17 0 013 4c0-.6.4-1 1-1h3.5c.6 0 1 .4 1 1 0 1.3.2 2.5.6 3.6.1.3 0 .7-.2 1z" fill="#fff"/></svg>
      <span>123-456-7890</span>
    </div>
    <div class="row" style="top:180px">
      <svg width="18" height="14" viewBox="0 0 18 14"><rect x="0" y="0" width="18" height="14" rx="1" fill="#fff"/><path d="M1 1l8 7 8-7" fill="none" stroke="#0b0b0b" stroke-width="1.6"/></svg>
      <span>support@emberly.com</span>
    </div>
    <span class="soc" style="left:883px"></span>
    <span class="soc" style="left:942px"></span>
    <span class="soc" style="left:1001px"></span>
    <span class="soc" style="left:1058px"></span>
    <p class="copy">COPYRIGHT © 2023 EMBERLY. ALL RIGHTS RESERVED.</p>
  </footer>

</div>
</body>
</html>
```